Card design for orthopaedic surgeons working as The Brightwater Joint Centre

Business cards, letterhead

Colors

Designer to choose colors to be used in the design.

Requirements
Must have
• Late addition.
• Cards letterhead must have logos of
• Crestmoor Lindell College of Surgeons
• Varenwood Bone Health Association
Nice to have
• Back of card to have space for appointment time to be added by hand and some blank space for writing incidental other notes.

```html
<!DOCTYPE html>
<html lang="en">
<head>
<meta charset="utf-8">
<title>The Brightwater Joint Centre – Stationery</title>
<link href="https://fonts.googleapis.com/css2?family=Montserrat:wght@400;500;600&family=Arimo:wght@400;700&display=swap" rel="stylesheet">
<style>
  :root {
    --navy: #0b3350;
    --sky: #5ba3d4;
    --paper: #f5f5f5;
    --backdrop: #e4e4e4;
    --ink: #1e1e1e;
  }
  * { box-sizing: border-box; margin: 0; padding: 0; }
  html, body { width: 1200px; height: 1200px; overflow: hidden; background: var(--backdrop); }
  .canvas { position: relative; width: 1200px; height: 1200px; }

  .sheet, .card { position: absolute; background: var(--paper); overflow: hidden; }

  .brand-name { font-family: 'Montserrat', sans-serif; font-weight: 400; color: var(--navy); white-space: nowrap; position: absolute; }

  .wave { position: absolute; left: 0; bottom: 0; display: block; }
  .wave .band { fill: var(--sky); }
  .wave .base, .wave .wedge { fill: var(--navy); }

  .seal { position: absolute; border-radius: 6px; background: linear-gradient(160deg, #d9c79e, #a9885a); }

  .contact { position: absolute; text-align: right; font-family: 'Montserrat', sans-serif; color: #fff; white-space: nowrap; }
  .contact .icon { display: inline-block; width: 1em; height: 1em; vertical-align: -0.12em; margin-left: 3px; }

  /* Letterhead */
  .letterhead { left: 98px; top: 124px; width: 677px; height: 957px; }
  .letterhead .brand-name { left: 47px; top: 70px; font-size: 21px; }
  .letter { position: absolute; left: 47px; top: 222px; width: 582px; font-family: 'Arimo', sans-serif; font-size: 10px; line-height: 13.7px; color: var(--ink); }
  .letter .date { margin-bottom: 14px; }
  .letter .recipient { margin-bottom: 28px; }
  .letter .salutation { font-weight: 700; margin-bottom: 27px; }
  .letter .body p { text-align: justify; margin-bottom: 13.7px; }
  .letter .closing { margin-top: 35px; }
  .letter .signature { width: 165px; height: 24px; margin: 20px 0 7px; border-radius: 4px; background: linear-gradient(90deg, rgba(30,30,30,.18), rgba(30,30,30,.06)); }
  .letterhead .seal-college { left: 54px; top: 848px; width: 53px; height: 62px; }
  .letterhead .seal-association { left: 125px; top: 851px; width: 67px; height: 58px; }
  .letterhead .contact { right: 48px; top: 872px; font-size: 10px; line-height: 13px; }
  .letterhead .contact .gap { margin-top: 4px; }

  /* Appointment card */
  .appointment { left: 823px; top: 277px; width: 290px; height: 176px; }
  .appointment .brand-name { left: 21px; top: 27px; font-size: 10.5px; }
  .appointment .seal-college { left: 201px; top: 13px; width: 28px; height: 33px; }
  .appointment .seal-association { left: 237px; top: 15px; width: 33px; height: 30px; }
  .appointment h2 { position: absolute; left: 0; right: 0; top: 62px; text-align: center; font-family: 'Montserrat', sans-serif; font-weight: 600; font-size: 10px; color: var(--navy); }
  .field { position: absolute; left: 22px; right: 20px; font-family: 'Montserrat', sans-serif; font-size: 7.5px; color: var(--navy); }
  .field .label { position: absolute; left: 0; bottom: 0; }
  .field .rule { position: absolute; left: 27px; right: 0; bottom: 0; border-bottom: 0.8px solid var(--sky); }
  .field .time { position: absolute; left: 158px; bottom: 0; }
  .field-name { top: 92px; height: 12px; }
  .field-date { top: 118px; height: 12px; }
  .field-note { top: 144px; height: 12px; }

  /* Business card */
  .business { left: 823px; top: 505px; width: 290px; height: 176px; }
  .business .brand-name { left: 20px; top: 30px; font-size: 11.5px; }
  .business .person { position: absolute; left: 20px; top: 81px; font-family: 'Montserrat', sans-serif; }
  .business .person .name { font-size: 9.5px; font-weight: 600; color: var(--sky); }
  .business .person .role { font-size: 7.5px; color: var(--navy); }
  .business .contact { right: 17px; top: 112px; font-size: 7.3px; line-height: 9.6px; }
  .business .contact .gap { margin-top: 3px; }
</style>
</head>
<body>
<div class="canvas">

  <section class="sheet letterhead">
    <div class="brand-name">The Brightwater Joint Centre</div>

    <div class="letter">
      <p class="date">November 12, 2019</p>
      <p class="recipient">Mr. Samuel Reed<br>President<br>Orchard Lane Corporation<br>111 Street Name, Suite#<br>City, State, 12345</p>
      <p class="salutation">Dear Mr. Samuel,</p>
      <div class="body">
        <p>Lorem ipsum dolor sit amet, consectetur adipiscing elit. Integer diam quam, egestas eu ultrices eu, suscipit ac sapien. Phasellus eu dui nisi. Nam et euismod diam, nec lobortis tortor. Donec et diam nulla. Aenean varius tincidunt convallis. Aliquam a tortor at lacus dictum aliquet. Nunc laoreet metus sapien, in scelerisque augue consectetur in.</p>
        <p>Fusce nec justo laoreet, egestas justo sed, aliquet sem. Pellentesque pharetra massa non orci bibendum semper. Pellentesque cursus eu lectus a consectetur. Nunc volutpat suscipit posuere. Vestibulum facilisis vel quam malesuada mattis. Nulla in mattis tellus. Maecenas tristique mauris vitae pharetra tincidunt. In ut ornare risus. Integer molestie vestibulum nisi, semper dapibus mi condimentum eu.</p>
        <p>Nullam sagittis elit libero, id fringilla est tincidunt eget. Donec in ipsum ultricies, consectetur quam vel, facilisis elit. Phasellus tincidunt congue risus vel luctus. Suspendisse ut mollis neque. Donec ornare orci in turpis vestibulum, in ultrices metus scelerisque. Pellentesque mattis mattis nunc, nec tincidunt lacus egestas id. Fusce facilisis sagittis neque sit amet vulputate. Aliquam ut eros lobortis tortor facilisis vehicula. Sed sed luctus leo, at laoreet sapien. Donec placerat adipiscing ligula non euismod. In lobortis pretium nisl id luctus.</p>
        <p>Integer gravida tincidunt nibh, scelerisque tincidunt turpis. Suspendisse potenti. Nunc hendrerit euismod lectus id elementum. Fusce vitae gravida velit, quis eleifend lectus. In imperdiet mauris eu dui viverra sagittis. Donec tempor dui diam, condimentum gravida lacus pretium a. Nullam fringilla augue quis arcu placerat scelerisque. Aliquam nec tincidunt augue, sit amet posuere ipsum.</p>
      </div>
      <p class="closing">Sincerely Yours,</p>
      <div class="signature" role="img" aria-label="Handwritten signature of Daniel Harper"></div>
      <p>Daniel Harper<br>Managing Director</p>
    </div>

    <svg class="wave" width="677" height="139" viewBox="0 0 677 139" aria-hidden="true">
      <path class="band" d="M0 106 C200 126 350 60 480 26 C560 8 620 5 677 7 L677 26 C620 25 570 28 510 38 C360 64 180 120 0 112Z"/>
      <path class="wedge" d="M0 84 C30 100 80 112 230 105 C150 113 50 112 0 102Z"/>
      <path class="base" d="M0 118 C180 128 360 70 520 44 C590 34 640 33 677 35 V139 H0Z"/>
    </svg>

    <div class="seal seal-college" role="img" aria-label="Crestmoor Lindell College of Surgeons badge"></div>
    <div class="seal seal-association" role="img" aria-label="Varenwood Bone Health Association badge"></div>

    <div class="contact">
      <p>48 Harbour View Road</p>
      <p>Lakeside, Florida, 33190</p>
      <p class="gap">(555) 014-2290<svg class="icon" viewBox="0 0 10 10"><path fill="#5ba3d4" d="M2 1 L3.6 1 L4.2 3 L3.2 3.8 C3.8 5 5 6.2 6.2 6.8 L7 5.8 L9 6.4 L9 8 C9 8.6 8.6 9 8 9 C4 9 1 6 1 2 C1 1.4 1.4 1 2 1Z"/></svg></p>
      <p>daniel@brightwaterjoint.com<svg class="icon" viewBox="0 0 10 10"><rect x="1" y="2.5" width="8" height="5.5" fill="none" stroke="#5ba3d4" stroke-width="0.9"/><path d="M1 2.5 L5 5.6 L9 2.5" fill="none" stroke="#5ba3d4" stroke-width="0.9"/></svg></p>
      <p>www.brightwaterjoint.com<svg class="icon" viewBox="0 0 10 10"><g fill="none" stroke="#5ba3d4" stroke-width="0.8"><circle cx="5" cy="5" r="3.8"/><ellipse cx="5" cy="5" rx="1.7" ry="3.8"/><path d="M1.2 5 H8.8"/></g></svg></p>
    </div>
  </section>

  <section class="card appointment">
    <div class="brand-name">The Brightwater Joint Centre</div>
    <div class="seal seal-college" role="img" aria-label="Crestmoor Lindell College of Surgeons badge"></div>
    <div class="seal seal-association" role="img" aria-label="Varenwood Bone Health Association badge"></div>
    <h2>Next Appointment</h2>
    <div class="field field-name"><span class="label">Name</span><span class="rule"></span></div>
    <div class="field field-date"><span class="label">Date</span><span class="rule"></span><span class="time">Time</span></div>
    <div class="field field-note"><span class="label">Note</span><span class="rule"></span></div>
  </section>

  <section class="card business">
    <div class="brand-name">The Brightwater Joint Centre</div>
    <div class="person">
      <p class="name">Daniel Harper</p>
      <p class="role">Managing Director</p>
    </div>
    <svg class="wave" width="290" height="176" viewBox="0 0 290 176" aria-hidden="true">
      <path class="band" d="M0 136 C80 148 150 105 210 80 C245 68 270 65 290 66 L290 76 C265 76 240 80 205 93 C140 118 70 148 0 142Z"/>
      <path class="wedge" d="M0 124 C20 135 50 140 100 137 C60 143 20 141 0 133Z"/>
      <path class="base" d="M0 146 C80 150 150 118 200 100 C240 88 265 86 290 87 V176 H0Z"/>
    </svg>
    <div class="contact">
      <p>48 Harbour View Road</p>
      <p>Lakeside, Florida, 33190</p>
      <p class="gap">(555) 014-2290<svg class="icon" viewBox="0 0 10 10"><path fill="#5ba3d4" d="M2 1 L3.6 1 L4.2 3 L3.2 3.8 C3.8 5 5 6.2 6.2 6.8 L7 5.8 L9 6.4 L9 8 C9 8.6 8.6 9 8 9 C4 9 1 6 1 2 C1 1.4 1.4 1 2 1Z"/></svg></p>
      <p>daniel@brightwaterjoint.com<svg class="icon" viewBox="0 0 10 10"><rect x="1" y="2.5" width="8" height="5.5" fill="none" stroke="#5ba3d4" stroke-width="0.9"/><path d="M1 2.5 L5 5.6 L9 2.5" fill="none" stroke="#5ba3d4" stroke-width="0.9"/></svg></p>
      <p>www.brightwaterjoint.com<svg class="icon" viewBox="0 0 10 10"><g fill="none" stroke="#5ba3d4" stroke-width="0.8"><circle cx="5" cy="5" r="3.8"/><ellipse cx="5" cy="5" rx="1.7" ry="3.8"/><path d="M1.2 5 H8.8"/></g></svg></p>
    </div>
  </section>

</div>
</body>
</html>
```